RESIDENTIAL CONSTRUCTION

We are a company that specializes in building custom residential homes, the design should also emphasize that quality and service is our priority.

Industry/Entity Type

Construction Company

Contact Information for Business Card

Contact Person: Marcus Lindqvist
Company Address: 273 West Alder Ave San Jose , Ca 95380
Phone Number : 408-731-2946
Email Address: Stoneridgehomes517@mailvista.net

Font styles to use
Sans Serif

Colors
ec1f27

Requirements
Must have
• CSLB # 7362015
Nice to have
• needs to have same color as logo i uploaded, we will be printing these on a clear plastic card.

```html
<!DOCTYPE html>
<html lang="en">
<head>
<meta charset="utf-8">
<title>Stoneridge General Builders – Business Card</title>
<link href="https://fonts.googleapis.com/css2?family=Oswald:wght@500&family=Roboto:wght@400;500&display=swap" rel="stylesheet">
<style>
  :root{
    --backdrop:#1a1a1a;
    --card:#2a2a2b;
    --edge:#ec1f27;
    --brand-red:#ec1f27;
    --text-light:#e9e9e9;
    --silver:#d4d4d4;
    --divider:#4a4a4b;
  }
  *{margin:0;padding:0;box-sizing:border-box}
  html,body{width:1200px;height:800px;overflow:hidden;background:var(--backdrop)}
  .stage{position:relative;width:1200px;height:800px;display:flex;flex-direction:column;align-items:center;justify-content:center;gap:44px}
  .card{position:relative;width:560px;height:320px;background:var(--card);border-radius:3px;box-shadow:0 0 0 2px var(--edge),0 14px 30px rgba(0,0,0,.55);overflow:hidden}
  .wordmark{display:flex;align-items:center;gap:12px;font-family:'Oswald',sans-serif;font-weight:500;text-transform:uppercase;line-height:1}
  .wordmark-square{width:16px;height:16px;flex:none}
  .wordmark-name{display:flex;flex-direction:column;letter-spacing:.04em}
  .wordmark-name .line-main{font-size:46px}
  .wordmark-name .line-sub{font-size:17px;letter-spacing:.28em;margin-top:6px}

  .card-front{display:flex;align-items:center;justify-content:center}
  .card-front .wordmark{color:var(--silver)}
  .card-front .wordmark-square{background:var(--silver)}

  .card-back{display:flex;align-items:center;padding:0 34px 0 48px}
  .card-back .wordmark{color:var(--brand-red)}
  .card-back .wordmark-name .line-main{font-size:36px}
  .card-back .wordmark-name .line-sub{font-size:13px;letter-spacing:.22em}
  .card-back .wordmark-square{background:var(--brand-red);width:13px;height:13px}
  .divider{width:1px;height:140px;background:var(--divider);margin:0 20px 0 24px}
  .contact{font-family:'Roboto',sans-serif;color:var(--text-light);font-size:12.5px;line-height:1.45}
  .contact-name{font-weight:500;color:var(--brand-red);font-size:18px;letter-spacing:.02em;text-transform:uppercase;margin-bottom:6px}
  .contact-list{list-style:none;margin-top:2px}
  .contact-list li{display:flex;align-items:center;gap:7px}
  .contact-list svg{width:11px;height:11px;flex:none;fill:var(--brand-red)}
</style>
</head>
<body>
<main class="stage">
  <section class="card card-front" aria-label="Card front">
    <div class="wordmark">
      <span class="wordmark-square" aria-hidden="true"></span>
      <span class="wordmark-name">
        <span class="line-main">Stoneridge</span>
        <span class="line-sub">General Builders</span>
      </span>
    </div>
  </section>

  <section class="card card-back" aria-label="Card back">
    <div class="wordmark">
      <span class="wordmark-square" aria-hidden="true"></span>
      <span class="wordmark-name">
        <span class="line-main">Stoneridge</span>
        <span class="line-sub">General Builders</span>
      </span>
    </div>
    <div class="divider" aria-hidden="true"></div>
    <div class="contact">
      <p class="contact-name">Marcus Lindqvist</p>
      <p>273 West Alder Ave San Jose</p>
      <p>Ca 95380</p>
      <p>CSLB # 7362015</p>
      <ul class="contact-list">
        <li><svg viewBox="0 0 24 24" aria-hidden="true"><path d="M6.6 10.8a15.1 15.1 0 0 0 6.6 6.6l2.2-2.2c.3-.3.7-.4 1-.2 1.1.4 2.3.6 3.6.6.6 0 1 .4 1 1V20c0 .6-.4 1-1 1A17 17 0 0 1 3 4c0-.6.4-1 1-1h3.5c.6 0 1 .4 1 1 0 1.2.2 2.4.6 3.6.1.3 0 .7-.2 1z"/></svg>408-731-2946</li>
        <li><svg viewBox="0 0 24 24" aria-hidden="true"><path d="M2 5h20v14H2zm2 2v.5l8 5 8-5V7l-8 5z"/></svg>Stoneridgehomes517@mailvista.net</li>
        <li><svg viewBox="0 0 24 24" aria-hidden="true"><path d="M12 2a10 10 0 1 0 0 20 10 10 0 0 0 0-20zm6.9 9h-3a15 15 0 0 0-1.3-5.6A8 8 0 0 1 18.9 11zM12 4.1c.9 1.2 1.7 3.6 1.9 6.9h-3.8c.2-3.3 1-5.7 1.9-6.9zM9.4 5.4A15 15 0 0 0 8.1 11h-3a8 8 0 0 1 4.3-5.6zM5.1 13h3a15 15 0 0 0 1.3 5.6A8 8 0 0 1 5.1 13zm6.9 6.9c-.9-1.2-1.7-3.6-1.9-6.9h3.8c-.2 3.3-1 5.7-1.9 6.9zm2.6-1.3a15 15 0 0 0 1.3-5.6h3a8 8 0 0 1-4.3 5.6z"/></svg>www.stoneridgebuilders.com</li>
      </ul>
    </div>
  </section>
</main>
</body>
</html>
```